Veltrano.co - Polar Expeditions Specialists

We need a modern, visually striking business card for Veltrano.co, a company specialized in selling expedition cruises to the most remote regions on Earth, with a focus on the Arctic and Antarctica. The design should instantly communicate that the cardholder is an expert in polar travel. Use clean, premium aesthetics with cool tones like icy blue and white, possibly incorporating polar imagery (ice, glaciers, penguins, etc.)

Attached the logo

Contact Information for Business Card

Feels high-end and trustworthy.. Visually memorable — encourages people to keep it

Colors
0054AA
0677BA
7BADD7
CADEEF
E8F1F8

Requirements
Must have
• ice, glaciers, penguins, montains
Nice to have
• modern, transparente,

```html
<!DOCTYPE html>
<html lang="en">
<head>
<meta charset="UTF-8">
<title>Veltrano.co – Business Card</title>
<link href="https://fonts.googleapis.com/css2?family=Arimo:wght@400;700&family=Poppins:wght@600;700&display=swap" rel="stylesheet">
<style>
  :root {
    --card-blue: #2f6dab;
    --brand-blue: #2f6dab;
    --card-white: #f4f5f7;
    --ink-light: #ffffff;
    --backdrop: #d3d4d6;
  }
  * { margin: 0; padding: 0; box-sizing: border-box; }
  html, body {
    width: 1200px; height: 800px; overflow: hidden;
    background: var(--backdrop);
  }
  .stage {
    width: 1200px; height: 800px;
    display: flex; align-items: center; justify-content: center; gap: 48px;
  }
  .card {
    width: 540px; height: 310px;
    border-radius: 24px;
    position: relative;
    overflow: hidden;
    box-shadow: 0 6px 18px rgba(0,0,0,0.18);
  }
  /* Back side */
  .card--back {
    background: var(--card-blue);
    color: var(--ink-light);
    font-family: "Arimo", Arial, sans-serif;
  }
  .back-mark {
    position: absolute; left: 48px; top: 190px;
    font-family: "Poppins", sans-serif;
    font-weight: 700; font-size: 28px; line-height: 1;
    color: var(--ink-light);
    display: flex; align-items: center; gap: 10px;
  }
  .back-mark__dot {
    width: 14px; height: 14px; border-radius: 50%; background: var(--ink-light);
  }
  .contact {
    position: absolute; left: 312px; top: 48px;
  }
  .contact__name { font-size: 20px; font-weight: 700; line-height: 1.1; }
  .contact__role { font-size: 13px; margin-bottom: 14px; }
  .contact__address { font-size: 13px; line-height: 1.35; margin-bottom: 14px; }
  .contact__lines { list-style: none; font-size: 13px; line-height: 1.35; }
  .contact__lines b { display: inline-block; width: 24px; }
  /* Front side */
  .card--front {
    background: var(--card-white);
    display: flex; flex-direction: column; align-items: center; justify-content: center;
    font-family: "Poppins", sans-serif;
    color: var(--brand-blue);
  }
  .front-mark__dot {
    width: 18px; height: 18px; border-radius: 50%;
    background: var(--brand-blue);
    margin-bottom: 14px;
  }
  .wordmark { font-size: 48px; font-weight: 700; line-height: 1; letter-spacing: -0.5px; }
  .tagline { font-size: 14px; font-weight: 600; margin-top: 8px; }
</style>
</head>
<body>
<main class="stage">
  <section class="card card--back">
    <div class="back-mark"><span class="back-mark__dot"></span>Veltrano.co</div>
    <div class="contact">
      <p class="contact__name">Jonas Hartley</p>
      <p class="contact__role">President</p>
      <p class="contact__address">2917 Larchmont Avenue<br>Cedar Hollow, NY 11204</p>
      <ul class="contact__lines">
        <li><b>P :</b>(604) 5182-7730</li>
        <li><b>E :</b>name@veltrano.com</li>
        <li><b>W :</b>www.veltrano.com</li>
      </ul>
    </div>
  </section>
  <section class="card card--front">
    <span class="front-mark__dot"></span>
    <p class="wordmark">Veltrano.co</p>
    <p class="tagline">Polar Expeditions Specialists</p>
  </section>
</main>
</body>
</html>
```